Fun relaxed Travel Photography Business Card*

Require a fun, funky and quirky but rememberable business card for a travel photographer

Industry/Entity Type

Photographer

Contact Information for Business Card

Front Card

(my name) Lenn D.

Travel Photographer ( small under travel photographer) “self-proclaimed”

(website logo) wanderingsoflenn.net

(Instagram logo) @wanderings_of_lenn

(Instagram logo) @wanderings_of_lenn_2.0 (backup for when Instagram puts Lenn on timeout for bad behaviour)

Tel: N/A (removing the potential awkwardness of me not replying)

Email: (see above)

Back Card

Annoying strangers since 1991

(Bottom right corner) “p.s. travelling made me fatTER”

Font styles to use
Serif

Colors

Designer to choose colors to be used in the design.

Requirements
Must have
• a camera
• a similar cartoon version of me as the "logo" see attached files, try to make as similar as possible

```html
<!DOCTYPE html>
<html lang="en">
<head>
<meta charset="utf-8">
<title>Lenn D. – Travel Photographer Business Card</title>
<link rel="stylesheet" href="https://fonts.googleapis.com/css2?family=Montserrat:wght@400;500;600;700&display=swap">
<style>
  :root {
    --stage: #2a2d31;
    --card-white: #ffffff;
    --card-black: #141414;
    --ink: #1c1c1c;
    --ink-soft: #5a5a5a;
    --silver: #cfcfcf;
    --paper-white: #f4f4f4;
  }
  * { box-sizing: border-box; margin: 0; padding: 0; }
  html, body {
    width: 1200px; height: 900px; overflow: hidden;
    background: var(--stage);
  }
  .stage {
    position: relative; width: 1200px; height: 900px;
    display: flex; flex-direction: column; align-items: center; justify-content: center; gap: 60px;
  }
  .card {
    position: relative; width: 630px; height: 360px;
    border-radius: 28px; overflow: hidden;
    font-family: "Montserrat", sans-serif;
  }

  /* front */
  .card--front { background: var(--card-white); color: var(--ink); }
  .avatar {
    position: absolute; left: 70px; top: 40px; width: 150px; height: 280px;
    border-radius: 60px 60px 20px 20px;
    background: linear-gradient(180deg, #5a3a28 0%, #2d4f9a 35%, #d9c7a6 70%, #5a3a28 100%);
  }
  .identity { position: absolute; right: 48px; top: 44px; text-align: right; }
  .identity__name { font-size: 34px; font-weight: 500; letter-spacing: 1px; text-transform: uppercase; }
  .identity__role { font-size: 15px; font-weight: 600; letter-spacing: 1px; text-transform: uppercase; margin-top: 2px; }
  .identity__note { font-size: 13px; font-weight: 500; letter-spacing: 1px; text-transform: uppercase; color: var(--ink-soft); margin-top: 2px; }
  .contacts {
    position: absolute; right: 48px; bottom: 36px;
    list-style: none; text-align: right;
  }
  .contacts__item {
    display: flex; align-items: center; justify-content: flex-end; gap: 12px;
    font-size: 17px; line-height: 30px;
  }
  .contacts__icon { width: 20px; height: 20px; flex: none; }

  /* back */
  .card--back { background: var(--card-black); color: var(--silver); }
  .camera-motif {
    position: absolute; left: 210px; top: 40px; width: 230px; height: 230px; border-radius: 50%;
    background: radial-gradient(circle, rgba(255,255,255,0.07) 0%, rgba(255,255,255,0.03) 55%, rgba(255,255,255,0) 72%);
  }
  .tagline {
    position: absolute; left: 40px; right: 40px; top: 134px; text-align: center;
    font-weight: 600; font-size: 30px;
    letter-spacing: 1px; text-transform: uppercase; color: var(--silver);
  }
  .postscript {
    position: absolute; right: 40px; bottom: 32px;
    font-size: 17px; font-weight: 400; color: var(--paper-white);
  }
  .postscript strong { font-weight: 700; }
</style>
</head>
<body>
<main class="stage">
  <section class="card card--front" aria-label="Business card front">
    <div class="avatar" role="img" aria-label="Cartoon figure of Lenn in a floral shirt, shorts and sunglasses"></div>
    <div class="identity">
      <h1 class="identity__name">Lenn D.</h1>
      <p class="identity__role">Travel Photographer</p>
      <p class="identity__note">(Self-proclaimed)</p>
    </div>
    <ul class="contacts">
      <li class="contacts__item">wanderingsoflenn.net
        <svg class="contacts__icon" viewBox="0 0 20 20" aria-hidden="true" fill="none" stroke="#1c1c1c" stroke-width="1.6">
          <circle cx="10" cy="10" r="8.5"/><ellipse cx="10" cy="10" rx="3.6" ry="8.5"/><path d="M1.5 10h17M3 5.5h14M3 14.5h14"/>
        </svg>
      </li>
      <li class="contacts__item">@wanderings_of_lenn
        <svg class="contacts__icon" viewBox="0 0 20 20" aria-hidden="true"><rect x="2" y="2" width="16" height="16" rx="2" fill="#1c1c1c"/></svg>
      </li>
      <li class="contacts__item">@wanderings_of_lenn_2.0
        <svg class="contacts__icon" viewBox="0 0 20 20" aria-hidden="true"><rect x="2" y="2" width="16" height="16" rx="2" fill="#1c1c1c"/></svg>
      </li>
      <li class="contacts__item">N/A
        <svg class="contacts__icon" viewBox="0 0 20 20" aria-hidden="true">
          <path d="M5 2.5l3 3.2-1.6 2.2c1 2.2 2.6 3.8 4.8 4.8l2.2-1.6 3.2 3-2 2.6C8.6 16.5 3.5 11.4 2.4 5.3z" fill="#1c1c1c"/>
        </svg>
      </li>
      <li class="contacts__item">N/A
        <svg class="contacts__icon" viewBox="0 0 20 20" aria-hidden="true">
          <rect x="1.5" y="4" width="17" height="12" fill="#1c1c1c"/><path d="M1.5 4.5L10 11l8.5-6.5" fill="none" stroke="#fff" stroke-width="1.4"/>
        </svg>
      </li>
    </ul>
  </section>

  <section class="card card--back" aria-label="Business card back">
    <div class="camera-motif" role="img" aria-label="Faint line drawing of a camera"></div>
    <p class="tagline">Annoying strangers since 1991</p>
    <p class="postscript">p.s. travelling made me fat<strong>TER</strong></p>
  </section>
</main>
</body>
</html>
```